Business cards for a fun web development agency

Hi,I am building a web development agency. You can read about it on the website http://kite-loft.examplehost.com. Basically, I want to focus on free and open source products and stay as far away from the corporate business feeling as possible. I want to build a community so I want the business card to feel fun and approachable (at the risk of professional if need be). I am uploading some of my image assets in various file formats. Feel free to use them or make your own if you want just keeping in theme with the website.
Industry/Entity Type
Building
Contact Information for Business Card
Company Name: Boat ShedWebsite: www.kiteloftdev.example (it's currently in alpha on http://kite-loft.examplehost.com if you want to see the them we are trying to capture)My name is: Banner B. SchaferMy email: banner@boatsheddev.comMy phone: 0431 587 904
Look and feel

```html
<!DOCTYPE html>
<html lang="en">
<head>
<meta charset="utf-8">
<title>Kite Loft business cards</title>
<link rel="stylesheet" href="https://fonts.googleapis.com/css2?family=Roboto:wght@400;500&display=swap">
<style>
  :root {
    --backdrop: #ece9e4;
    --brand-blue: #1aa7c9;
    --brand-blue-deep: #1290b3;
    --card-white: #ffffff;
    --card-grey: #f1f1f1;
    --shadow: rgba(40, 30, 20, 0.22);
  }
  * { margin: 0; padding: 0; box-sizing: border-box; }
  html, body {
    width: 1200px;
    height: 885px;
    overflow: hidden;
    background: var(--backdrop);
  }
  .sheet {
    width: 1200px;
    height: 885px;
    display: flex;
    flex-direction: column;
    align-items: center;
    justify-content: center;
    gap: 48px;
  }
  .card {
    width: 630px;
    height: 360px;
    border-radius: 4px;
    overflow: hidden;
    position: relative;
    box-shadow: 0 10px 26px var(--shadow);
    font-family: "Roboto", Arial, sans-serif;
  }

  /* Company name: plain text in the card's own font */
  .company-name {
    font-weight: 500;
    font-size: 56px;
    line-height: 1.1;
    letter-spacing: 0;
    white-space: nowrap;
  }

  /* Front */
  .card-front {
    display: flex;
    background: linear-gradient(180deg, var(--card-white), var(--card-grey));
  }
  .front-band {
    width: 78px;
    background: linear-gradient(180deg, var(--brand-blue), var(--brand-blue-deep));
  }
  .front-body {
    flex: 1;
    padding: 44px 40px 0 32px;
    color: var(--brand-blue);
  }
  .holder-name {
    margin-top: 24px;
    font-size: 33px;
    font-weight: 400;
  }
  .contact-list {
    list-style: none;
    margin-top: 22px;
    font-size: 21px;
    line-height: 1.45;
  }

  /* Back */
  .card-back {
    background: linear-gradient(160deg, var(--brand-blue), var(--brand-blue-deep));
    display: flex;
    flex-direction: column;
  }
  .back-main {
    flex: 1;
    display: flex;
    align-items: center;
    justify-content: center;
    color: var(--card-white);
  }
  .back-main .company-name { font-size: 68px; }
  .tagline-strip {
    height: 60px;
    background: linear-gradient(180deg, var(--card-white), var(--card-grey));
    display: flex;
    align-items: center;
    justify-content: center;
    font-size: 17px;
    color: var(--brand-blue-deep);
    letter-spacing: 0.3px;
  }
  .tagline-divider { margin: 0 10px; }
</style>
</head>
<body>
<main class="sheet">
  <section class="card card-front" aria-label="Business card front">
    <div class="front-band"></div>
    <div class="front-body">
      <p class="company-name">Kite Loft</p>
      <p class="holder-name">Corwin T. Aldous</p>
      <ul class="contact-list">
        <li>0431 587 904</li>
        <li>www.kiteloftdev.example</li>
        <li>corwin@kiteloftdev.example</li>
      </ul>
    </div>
  </section>

  <section class="card card-back" aria-label="Business card back">
    <div class="back-main">
      <p class="company-name">Kite Loft</p>
    </div>
    <div class="tagline-strip">
      <span>Consulting For Developers</span><span class="tagline-divider">|</span><span>Web Development For Muggles</span>
    </div>
  </section>
</main>
</body>
</html>
```